Yacht Charter Broker needs a magazine page design

We are a travel agent for yachts called Velmora Yacht Charters. www.velmoracharters.example We are advertising in a magazine at the world championship saddlebred horse show - https://brindlefieldexpo.example/ - and need a high-end luxury feeling magazine page.

Target Market(s)

Vacation goers looking to charter a crewed yacht.

Industry/Entity Type

Travel Agent

Requirements
Must have
• luxury feel. logo. website and social media icons if you feel necessary. Our motto is: Inhale. Exhale. Sail.
• Catamaran picture, snorkeling and other island, water looking pictures.
Nice to have
• Open to your design.
Should not have
• Nothing comes to mind.

```html
<!DOCTYPE html>
<html lang="en">
<head>
<meta charset="utf-8">
<title>Velmora Yacht Charters – Magazine Page</title>
<link rel="stylesheet" href="https://fonts.googleapis.com/css2?family=Montserrat:wght@400;600;700&family=Great+Vibes&family=Cinzel:wght@400&display=swap">
<style>
  :root {
    --backdrop: #8e9290;
    --ink: #1f2430;
    --sky: #ece4ee;
    --haze: #d9c8d6;
    --rock: #9d8479;
    --rock-dark: #6e5a57;
    --forest: #3f5a3a;
    --lake: #3fb6bd;
    --lake-light: #5cc3c7;
  }
  * { margin: 0; padding: 0; box-sizing: border-box; }
  html, body {
    width: 1200px; height: 863px; overflow: hidden;
    background: var(--backdrop);
  }
  .page {
    position: absolute;
    left: 283px; top: 20px;
    width: 634px; height: 823px;
    overflow: hidden;
    box-shadow: 0 6px 24px rgba(0,0,0,.25);
    font-family: "Montserrat", sans-serif;
    color: var(--ink);
  }
  .scenery {
    position: absolute; inset: 0;
    background: linear-gradient(180deg,
      var(--sky) 0%, var(--haze) 18%, var(--rock) 32%, var(--rock-dark) 44%,
      #c9b3a6 52%, var(--forest) 60%, var(--lake) 66%, var(--lake-light) 100%);
  }
  .headline {
    position: absolute; top: 34px; left: 0; right: 0;
    text-align: center;
  }
  .headline .kicker {
    font-size: 17px; letter-spacing: 2px; font-weight: 400;
    line-height: 1.35;
  }
  .headline .kicker-line {
    display: flex; align-items: center; justify-content: center; gap: 14px;
  }
  .headline .kicker-line::before,
  .headline .kicker-line::after {
    content: ""; width: 130px; height: 1px; background: var(--ink); opacity: .7;
  }
  .headline .script {
    font-family: "Great Vibes", cursive;
    font-size: 96px; line-height: 1; margin-top: -4px;
  }
  .brand {
    position: absolute; top: 560px; left: 0; right: 0; text-align: center;
  }
  .brand .name {
    font-family: "Cinzel", serif; font-size: 38px; letter-spacing: 6px;
  }
  .brand .tag {
    font-family: "Cinzel", serif; font-size: 10px; letter-spacing: 4px; margin-top: -2px;
  }
  .motto {
    position: absolute; top: 636px; left: 0; right: 0; text-align: center;
    font-weight: 600; font-size: 36px; letter-spacing: 1px;
  }
  .contact {
    position: absolute; top: 700px; left: 90px; right: 90px; text-align: center;
  }
  .contact .rule { height: 1px; background: var(--ink); opacity: .6; }
  .contact .web { font-size: 24px; padding: 8px 0; letter-spacing: .5px; }
  .social {
    display: flex; justify-content: center; gap: 8px; margin-top: 12px;
  }
  .social span {
    width: 24px; height: 24px; border-radius: 50%; background: var(--ink);
  }
</style>
</head>
<body>
  <main class="page">
    <div class="scenery" role="img" aria-label="Photograph of rugged mountains above a turquoise alpine lake with pine forest"></div>

    <header class="headline">
      <p class="kicker kicker-line">WE HAVE THE PERFECT YACHT</p>
      <p class="kicker">FOR YOUR NEXT</p>
      <p class="script">Adventure.</p>
    </header>

    <div class="brand">
      <p class="name">VELMORA</p>
      <p class="tag">YACHT CHARTER BROKER</p>
    </div>

    <p class="motto">INHALE • EXHALE • SAIL</p>

    <footer class="contact">
      <div class="rule"></div>
      <p class="web">www.velmoracharters.example</p>
      <div class="rule"></div>
      <div class="social" aria-label="Social media links">
        <span></span><span></span><span></span><span></span>
      </div>
    </footer>
  </main>
</body>
</html>
```